STOP THE LAWSUITS

I'm virtually ready to launch my site, but I have a number of edits and modifications that need to be implemented. More importantly, I'm always looking to improve my site, particularly now that I am making my proverbial "FIRST IMPRESSION." Thus, I'm willing to see if there is someone who can add creativity and perhaps improve what I already have, particularly on the All Important Front Page.

```html
<!DOCTYPE html>
<html lang="en">
<head>
<meta charset="utf-8">
<title>Harlow Legal – Turning Challenges into Legal Triumphs</title>
<link href="https://fonts.googleapis.com/css2?family=Fira+Sans:wght@400;500;600&family=Roboto:wght@400;500;700&display=swap" rel="stylesheet">
<style>
:root{
  --navy:#163a52;
  --navy-dark:#0f2b3f;
  --title:#1d3c6b;
  --red:#a50a14;
  --blue:#2f80ed;
  --gray-bg:#f4f4f4;
  --text:#8a8a8a;
  --dark:#222;
  --footer:#1f242b;
  --footer-line:#343a42;
  --white:#fff;
}
*{box-sizing:border-box;margin:0;padding:0}
html,body{width:1200px;height:4641px;overflow:hidden}
body{position:relative;font-family:"Roboto",Arial,sans-serif;color:var(--dark);background:var(--white)}
.abs{position:absolute}
h1,h2,h3,h4{font-family:"Fira Sans",Arial,sans-serif;font-weight:600}
a{color:inherit;text-decoration:none}

/* header */
.topbar{left:0;top:0;width:1200px;height:29px;background:var(--navy-dark)}
.topbar-white{left:0;top:0;width:400px;height:29px;background:var(--white);clip-path:polygon(0 0,100% 0,92% 100%,0 100%)}
.topbar span{position:absolute;top:8px;font-size:10px;color:var(--white);font-weight:500}
.navbar{left:0;top:29px;width:1200px;height:50px;background:var(--white);box-shadow:0 1px 3px rgba(0,0,0,.08)}
.brand{left:136px;top:35px;display:flex;align-items:center;gap:8px;font-family:"Fira Sans",sans-serif;font-weight:600;font-size:15px;color:var(--title)}
.brand i{width:28px;height:28px;border-radius:50%;background:var(--red);display:block}
.nav a{position:absolute;top:50px;font-size:11.5px;color:#555}
.nav a.active{color:var(--dark);font-weight:700}

/* hero */
.hero{left:0;top:79px;width:1200px;height:633px;background:linear-gradient(100deg,#2b3c4e 0%,#4a5d6e 45%,#6e7b84 100%)}
.hero-overlay{left:0;top:79px;width:1200px;height:633px;background:linear-gradient(90deg,rgba(17,32,48,.7),rgba(17,32,48,.15))}
.eyebrow{left:110px;top:268px;color:var(--white);font-size:13px;display:flex;align-items:center;gap:10px}
.eyebrow b{display:block;width:46px;height:1px;background:var(--white)}
.hero h1{left:110px;top:320px;width:600px;font-size:44px;line-height:57px;color:var(--white)}
.hero-text{left:110px;top:476px;width:420px;font-size:13px;line-height:22px;color:var(--white)}
.btn{display:flex;align-items:center;justify-content:center;font-family:"Fira Sans",sans-serif;font-weight:600;font-size:13px;color:var(--white);border-radius:4px}
.hero-btn{left:110px;top:556px;width:168px;height:46px;background:var(--blue)}

/* section common */
.section-title{width:1200px;text-align:center;font-size:31px;color:var(--title)}
.section-lead{width:1200px;text-align:center;font-size:12.5px;line-height:22px;color:var(--text)}

/* why choose */
.why{left:0;top:712px;width:1200px;height:609px;background:var(--gray-bg)}
.feature{top:970px;width:235px;height:216px;background:var(--white);box-shadow:0 2px 8px rgba(0,0,0,.1);border-radius:3px;text-align:center;padding-top:34px}
.feature svg{width:40px;height:40px}
.feature h3{font-size:17.5px;line-height:25px;color:var(--title);margin-top:8px}
.feature p{font-size:12.5px;line-height:21px;color:var(--text);margin-top:8px}
.feature.is-active{background:var(--navy)}
.feature.is-active h3,.feature.is-active p{color:var(--white)}
.why-btn{left:522px;top:1225px;width:170px;height:46px;background:var(--red)}

/* leading */
.lead-band{left:281px;top:1321px;width:919px;height:469px;background:var(--navy)}
.lead-photo{left:0;top:1387px;width:584px;height:447px;background:linear-gradient(120deg,#d9dde0 0%,#a7adb2 55%,#5b6268 100%)}
.lead h2{left:633px;top:1412px;font-size:31px;color:var(--white)}
.lead p{left:631px;width:430px;font-size:12.5px;line-height:22px;color:var(--white)}
.lead-btn{left:631px;top:1653px;width:156px;height:42px;background:var(--red);gap:12px}

/* services */
.service-photo{top:2063px;width:321px;height:237px;background:linear-gradient(110deg,#cfd3d6 0%,#8c8f8f 40%,#4b4f55 70%,#b9bec2 100%)}
.service-card{top:2240px;width:286px;height:203px;background:var(--white);box-shadow:0 2px 8px rgba(0,0,0,.1);padding:26px 40px 0 40px}
.service-card h3{font-size:21px;color:var(--title)}
.service-card p{font-size:12.5px;line-height:22px;color:var(--text);margin-top:8px}
.service-card a{display:block;margin-top:8px;font-size:10.5px;font-weight:700;color:var(--red)}
.service-card.is-active{background:var(--navy);padding-left:34px}
.service-card.is-active h3,.service-card.is-active p,.service-card.is-active a{color:var(--white)}

/* cta */
.cta{left:0;top:2514px;width:1200px;height:295px;background:linear-gradient(90deg,#24384c,#3c5064 55%,#2b3f52)}
.cta-overlay{left:0;top:2514px;width:1200px;height:295px;background:rgba(26,44,62,.55)}
.cta-phone{top:2562px;width:1200px;text-align:center;font-family:"Fira Sans",sans-serif;font-weight:500;font-size:23px;color:var(--white)}
.cta h2{top:2604px;width:1200px;text-align:center;font-size:32px;color:var(--white)}
.cta .section-lead{color:#e6e6e6}
.cta-btn{left:521px;top:2721px;width:167px;height:45px;border:1.5px solid var(--white);background:transparent}

/* reviews */
.review{top:3042px;width:494px;height:256px;background:var(--gray-bg)}
.review .rule{position:absolute;left:62px;top:40px;width:2px;height:178px;background:#2a4a80}
.review .quote{position:absolute;left:37px;top:104px;width:52px;height:52px;border-radius:50%;background:var(--red);border:4px solid var(--white);box-shadow:0 0 0 1px #d8d8d8;display:flex;align-items:center;justify-content:center;color:var(--white);font:700 30px/1 "Fira Sans",sans-serif}
.review .stars{position:absolute;left:114px;top:40px;color:#f0602a;font-size:15px;letter-spacing:5px}
.review p{position:absolute;left:114px;top:84px;width:340px;font-size:12.5px;line-height:22px;color:var(--text)}
.review h4{position:absolute;left:114px;top:169px;font-size:17px;color:var(--dark);font-weight:500}
.review small{position:absolute;left:114px;top:195px;font-size:12px;color:#777}
.review .avatar{position:absolute;right:54px;top:160px;width:58px;height:58px;border-radius:50%;background:linear-gradient(135deg,#e5ded8,#b8aaa0)}
.dots{left:565px;top:3342px;display:flex;gap:10px}
.dots i{width:9px;height:9px;border-radius:50%;background:#f0602a;display:block}
.dots i.off{background:transparent;border:1.5px solid #f0602a}

/* contact */
.contact-bg{left:0;top:3391px;width:1200px;height:850px;background:var(--gray-bg)}
.contact-panel{left:88px;top:3597px;width:1020px;height:461px;background:var(--white);box-shadow:0 2px 8px rgba(0,0,0,.08)}
.contact-photo{left:88px;top:3597px;width:512px;height:461px;background:linear-gradient(110deg,#2e4762,#4f6a84 60%,#3a5470)}
.contact-overlay{left:88px;top:3597px;width:512px;height:461px;background:rgba(22,50,82,.6)}
.contact-info{left:176px;top:3660px;color:var(--white);font-family:"Fira Sans",sans-serif}
.contact-info h4{font-size:17px;font-weight:600}
.contact-info .call{font-size:20px;font-weight:600;margin-top:26px}
.contact-info .small{font-size:11.5px;font-weight:600;line-height:16px}
.socials{left:178px;top:3963px;display:flex;gap:11px}
.socials i{width:30px;height:30px;border-radius:50%;background:rgba(255,255,255,.35);display:block}
.socials i.on{background:var(--white)}
.form-title{left:687px;top:3654px;font-family:"Fira Sans",sans-serif;font-weight:500;font-size:17px;color:var(--title)}
.field{left:688px;width:332px;height:32px;background:var(--gray-bg);font-size:9.5px;color:#888;padding:11px 14px}
.submit{left:688px;top:3966px;width:110px;height:37px;background:var(--red);font-size:11px}

/* info strip */
.footer{left:0;top:4190px;width:1200px;height:451px;background:var(--footer)}
.strip{left:65px;top:4139px;width:1070px;height:105px;background:var(--red);border-radius:6px}
.strip-sep{top:4139px;width:24px;height:105px}
.strip-item{top:4167px;display:flex;gap:22px;color:var(--white);font-family:"Fira Sans",sans-serif}
.strip-item svg{width:52px;height:50px}
.strip-item h4{font-size:17px;font-weight:600}
.strip-item p{font-size:12px;margin-top:12px;font-weight:500}

.footer h4{position:absolute;top:4314px;font-size:18px;color:var(--white)}
.footer-text{left:67px;top:4380px;width:320px;font-size:12.5px;line-height:31px;color:var(--white)}
.readmore{left:67px;top:4492px;font-size:15px;color:#3fa3f0;text-decoration:underline}
.links a{position:absolute;font-size:12.5px;color:var(--white);text-decoration:underline}
.sub-text{left:797px;top:4386px;width:330px;font-size:14px;line-height:24px;color:var(--white)}
.sub-field{left:797px;top:4448px;width:275px;height:55px;background:var(--white);font-size:12px;color:#666;padding:20px 16px;border-radius:4px 0 0 4px}
.sub-btn{left:1072px;top:4448px;width:64px;height:55px;background:var(--red);border-radius:0 4px 4px 0}
.bottom{left:0;top:4579px;width:1200px;height:62px;border-top:1px solid var(--footer-line)}
.bottom-brand{left:118px;top:4597px;display:flex;align-items:center;gap:8px;font-family:"Fira Sans",sans-serif;font-weight:600;font-size:14px;color:var(--white)}
.bottom-brand i{width:26px;height:26px;border-radius:50%;background:var(--red);display:block}
.bottom-social{top:4579px;width:59px;height:62px;border-left:1px solid var(--footer-line);display:flex;align-items:center;justify-content:center}
.bottom-social i{width:14px;height:14px;border-radius:50%;background:#4a525c;display:block}
</style>
</head>
<body>

<!-- header -->
<div class="abs topbar">
  <span style="left:466px">&#9679; 48 Alder Lane, Riverton, RS 20418</span>
  <span style="left:703px">Follow Us:&nbsp;&nbsp;&#9675; &#9675; &#9675;</span>
  <span style="left:857px">GET QUOTATION</span>
</div>
<div class="abs topbar-white"></div>
<div class="abs navbar"></div>
<div class="abs brand"><i></i>Harlow Legal</div>
<nav class="nav">
  <a class="active" style="left:402px">Home</a>
  <a style="left:484px">About Us</a>
  <a style="left:565px">Services</a>
  <a style="left:640px">Team</a>
  <a style="left:715px">Gallery</a>
  <a style="left:788px">Solutions</a>
  <a style="left:865px">Contact Us</a>
</nav>

<!-- hero -->
<div class="abs hero" role="img" aria-label="Photo of a legal team meeting around a conference table"></div>
<div class="abs hero-overlay"></div>
<div class="hero">
  <div class="abs eyebrow">On the other hand <b></b></div>
  <h1 class="abs">Turning Challenges into Legal Triumphs</h1>
  <p class="abs hero-text">Lorem ipsum dolor sit amet, consectetur adipiscing elit, sed do eiusmod temp dipiscing elit, sed d</p>
  <a class="abs btn hero-btn">Contact Us</a>
</div>

<!-- why choose us -->
<div class="abs why"></div>
<h2 class="abs section-title" style="left:0;top:840px">Why Choose Us</h2>
<p class="abs section-lead" style="left:0;top:895px">Lorem ipsum dolor sit amet, consectetur adipiscing elit, sed do eiusmod tempor<br>incididunt ut labore et dolore magna aliqua. Ut enim ad min</p>

<div class="abs feature" style="left:92px">
  <svg viewBox="0 0 40 40" fill="none" stroke="#a50a14" stroke-width="2"><polygon points="20,6 32,14 29,30 11,30 8,14"/><circle cx="20" cy="6" r="2.5"/><circle cx="32" cy="14" r="2.5"/><circle cx="8" cy="14" r="2.5"/></svg>
  <h3>Client<br>Centric</h3>
  <p>Lorem ipsum dolor sit amet,<br>consectetur adipiscing</p>
</div>
<div class="abs feature is-active" style="left:351px">
  <svg viewBox="0 0 40 40" fill="none" stroke="#a50a14" stroke-width="2"><circle cx="20" cy="12" r="5"/><path d="M8 28h24M11 33h18M20 17v11"/></svg>
  <h3>Free<br>Consultation</h3>
  <p>Lorem ipsum dolor sit amet,<br>consectetur adipiscing</p>
</div>
<div class="abs feature" style="left:611px">
  <svg viewBox="0 0 40 40" fill="none" stroke="#a50a14" stroke-width="2"><path d="M8 30a13 13 0 1 1 24 0"/><path d="M20 26l5-9"/><circle cx="20" cy="26" r="2"/></svg>
  <h3>Minimize<br>Exposure</h3>
  <p>Lorem ipsum dolor sit amet,<br>consectetur adipiscing</p>
</div>
<div class="abs feature" style="left:870px">
  <svg viewBox="0 0 40 40" fill="none" stroke="#a50a14" stroke-width="2"><circle cx="20" cy="13" r="6"/><path d="M8 34c0-8 6-12 12-12s12 4 12 12z"/></svg>
  <h3>Affordable<br>Services</h3>
  <p>Lorem ipsum dolor sit amet,<br>consectetur adipiscing</p>
</div>
<a class="abs btn why-btn">Contact Us</a>

<!-- leading legal services -->
<div class="abs lead-band"></div>
<div class="abs lead-photo" role="img" aria-label="Photo of a lawyer holding a tablet in a bright office"></div>
<div class="lead">
  <h2 class="abs">Leading Legal Services</h2>
  <p class="abs" style="top:1466px">Lorem ipsum dolor sit amet, consectetur adipiscing elit, sed do eiusmod tempor incididunt ut labore et dolore magna aliqua. Ut e nim ad min veniam, quis nostrud ex.</p>
  <p class="abs" style="top:1541px">Lorem ipsum dolor sit amet, consectetur adipiscing elit, sed do eiusmod tempor incididunt ut labore et dolore magna aliqua. Ut e nim ad min veniam, quis nostrud ex. et dolore magna aliqua. Ut e nim ad min veniam, quis nostrud ex.</p>
  <a class="abs btn lead-btn">Contact us
    <svg width="18" height="14" viewBox="0 0 18 14" fill="none" stroke="#fff" stroke-width="2"><path d="M1 7h15M10 1l6 6-6 6"/></svg>
  </a>
</div>

<!-- services -->
<h2 class="abs section-title" style="left:0;top:1910px">Services We Offer</h2>
<p class="abs section-lead" style="left:0;top:1965px">Lorem ipsum dolor sit amet, consectetur adipiscing elit, sed do eiusmod tempor<br>incididunt ut labore et dolore magna aliqua. Ut enim ad min</p>

<div class="abs service-photo" style="left:92px" role="img" aria-label="Photo of two lawyers talking in an office"></div>
<div class="abs service-photo" style="left:440px" role="img" aria-label="Photo of two lawyers talking in an office"></div>
<div class="abs service-photo" style="left:787px" role="img" aria-label="Photo of two lawyers talking in an office"></div>

<div class="abs service-card" style="left:110px">
  <h3>Consultation</h3>
  <p>Lorem ipsum dolor sit amet, cons ectetur adipiscing elit, sed do eiu smod tempor incididunt ut labore et dolore magna aliqua.</p>
  <a>LEARN MORE</a>
</div>
<div class="abs service-card is-active" style="left:459px">
  <h3>Litigation</h3>
  <p>Lorem ipsum dolor sit amet, cons ectetur adipiscing elit, sed do eiu smod tempor incididunt ut labore et dolore magna aliqua.</p>
  <a>LEARN MORE</a>
</div>
<div class="abs service-card" style="left:805px">
  <h3>Collection Claims</h3>
  <p>Lorem ipsum dolor sit amet, cons ectetur adipiscing elit, sed do eiu smod tempor incididunt ut labore et dolore magna aliqua.</p>
  <a>LEARN MORE</a>
</div>

<!-- consultation cta -->
<div class="abs cta" role="img" aria-label="Photo of a lawyer meeting with a client"></div>
<div class="abs cta-overlay"></div>
<div class="cta">
  <div class="abs cta-phone">123-456-7890</div>
  <h2 class="abs">Get Free Consultation Today</h2>
  <p class="abs section-lead" style="left:0;top:2659px">Lorem ipsum dolor sit amet, consectetur adipiscing elit, sed do eiusmod tempor<br>incididunt ut labore et dolore magna aliqua. Ut enim ad min</p>
  <a class="abs btn cta-btn">Contact Us</a>
</div>

<!-- reviews -->
<h2 class="abs section-title" style="left:0;top:2892px">Client Reviews</h2>
<p class="abs section-lead" style="left:0;top:2945px">Lorem ipsum dolor sit amet, consectetur adipiscing elit, sed do eiusmod tempor<br>incididunt ut labore et dolore magna aliqua. Ut enim ad min</p>

<div class="abs review" style="left:90px">
  <span class="rule"></span><span class="quote">&#8221;</span>
  <span class="stars">★★★★★</span>
  <p>Lorem ipsum dolor sit amet, consectetur adipiscing elit, sed do eiusmod tempor incididunt ut labore et d olore magna aliqua.</p>
  <h4>Maren Holt</h4><small>Brook Hollow</small>
  <span class="avatar" role="img" aria-label="Client portrait"></span>
</div>
<div class="abs review" style="left:609px">
  <span class="rule"></span><span class="quote">&#8221;</span>
  <span class="stars">★★★★★</span>
  <p>Lorem ipsum dolor sit amet, consectetur adipiscing elit, sed do eiusmod tempor incididunt ut labore et d olore magna aliqua.</p>
  <h4>Maren Holt</h4><small>Brook Hollow</small>
  <span class="avatar" role="img" aria-label="Client portrait"></span>
</div>
<div class="abs dots"><i></i><i></i><i class="off"></i><i></i></div>

<!-- contact -->
<div class="abs contact-bg"></div>
<h2 class="abs section-title" style="left:0;top:3447px">Get in touch with us</h2>
<p class="abs section-lead" style="left:0;top:3501px">Lorem ipsum dolor sit amet, consectetur adipiscing elit, sed do eiusmod tempor<br>incididunt ut labore et dolore magna aliqua. Ut enim ad min</p>

<div class="abs contact-panel"></div>
<div class="abs contact-photo" role="img" aria-label="Photo of a lawyer reviewing documents"></div>
<div class="abs contact-overlay"></div>
<div class="abs contact-info">
  <h4>CONTACT US</h4>
  <div class="call">Call: 0123456789</div>
  <div class="small" style="margin-top:6px">info@company.com</div>
  <div class="small" style="margin-top:26px">Address:<br>SOME PLACE<br>51100 Road</div>
  <div class="small" style="margin-top:24px">Operating Hours<br>Monday to Saturday: 9:00 - 18:00<br>Sunday: Closed</div>
</div>
<div class="abs socials"><i></i><i class="on"></i><i></i><i></i></div>

<div class="abs form-title">FREE CONSULTATION</div>
<div class="abs field" style="top:3706px">Your Name</div>
<div class="abs field" style="top:3755px">Email</div>
<div class="abs field" style="top:3804px">Phone</div>
<div class="abs field" style="top:3854px;height:92px">Message</div>
<a class="abs btn submit">SUBMIT</a>

<!-- footer -->
<div class="abs footer"></div>
<div class="abs strip"></div>
<svg class="abs strip-sep" style="left:410px" viewBox="0 0 24 105" preserveAspectRatio="none" fill="none" stroke="#fff" stroke-width="2"><path d="M2 0l18 52L2 105"/></svg>
<svg class="abs strip-sep" style="left:767px" viewBox="0 0 24 105" preserveAspectRatio="none" fill="none" stroke="#fff" stroke-width="2"><path d="M2 0l18 52L2 105"/></svg>

<div class="abs strip-item" style="left:106px">
  <svg viewBox="0 0 52 50" fill="none" stroke="#fff" stroke-width="2"><path d="M26 34s10-10 10-18a10 10 0 0 0-20 0c0 8 10 18 10 18z"/><circle cx="26" cy="16" r="4"/><path d="M14 30L4 46h44L38 30"/></svg>
  <div><h4>Address</h4><p>123, City, Country</p></div>
</div>
<div class="abs strip-item" style="left:470px">
  <svg viewBox="0 0 52 50" fill="none" stroke="#fff" stroke-width="2"><rect x="8" y="4" width="22" height="42" rx="3"/><path d="M15 40h8M36 18a8 8 0 0 1 0 12M41 14a14 14 0 0 1 0 20"/></svg>
  <div><h4>Phone</h4><p>+123 456 78890</p></div>
</div>
<div class="abs strip-item" style="left:820px">
  <svg viewBox="0 0 52 50" fill="none" stroke="#fff" stroke-width="2"><rect x="6" y="16" width="40" height="28"/><path d="M6 16l20 16 20-16M12 16V6h28v10M18 12h16"/></svg>
  <div><h4>Email Contact</h4><p>info@company.com</p></div>
</div>

<h4 class="abs" style="left:67px;top:4314px;font-size:18px;color:#fff">About Company</h4>
<p class="abs footer-text">Lorem ipsum dolor sit amet, consectetur adipis cing elit, sed do eiusmod tempor incididunt ut labore et dolore magna aliqua.</p>
<a class="abs readmore">Read More</a>

<h4 class="abs" style="left:434px;top:4314px;font-size:18px;color:#fff">Useful Links</h4>
<div class="links">
  <a style="left:434px;top:4387px">About Us</a>
  <a style="left:434px;top:4420px">Projects</a>
  <a style="left:434px;top:4454px">Blog</a>
  <a style="left:434px;top:4488px">Contact Us</a>
  <a style="left:610px;top:4387px">Services</a>
  <a style="left:610px;top:4420px">Shop</a>
  <a style="left:610px;top:4454px">Privacy Policy</a>
  <a style="left:610px;top:4488px">Help Desk</a>
</div>

<h4 class="abs" style="left:797px;top:4314px;font-size:18px;color:#fff">Subscribe</h4>
<p class="abs sub-text">If you have any questions, Subscribe to our newsleeter to know more</p>
<div class="abs sub-field">Email</div>
<div class="abs btn sub-btn"><svg width="14" height="20" viewBox="0 0 14 20" fill="none" stroke="#fff" stroke-width="2.5"><path d="M3 2l8 8-8 8"/></svg></div>

<div class="abs bottom"></div>
<div class="abs bottom-brand"><i></i>Harlow Legal</div>
<div class="abs bottom-social" style="left:900px"><i></i></div>
<div class="abs bottom-social" style="left:959px"><i></i></div>
<div class="abs bottom-social" style="left:1018px"><i></i></div>
<div class="abs bottom-social" style="left:1077px;border-right:1px solid var(--footer-line)"><i></i></div>

</body>
</html>
```